LANTERN - and the quiet crafts of everyday life

I´m writing a book about CHANGE and the skills leaders needs to embody the transformation from being amanager to become leaders.
The title of the book in Icelandic is the same as the name of the project (which I want to be used on the designes is:) UPPSPRETTA
(with the subtitle:) og hugrekki hversdagsins

Change is not controlled or managed – Leading effective change is an art form which is one of the big reasons for why 70% of changes within companies fail. The main reason however, is that managers are tasked with managing and directing them. The art form of change is to put it in the hands of leaders who possess the emotional intelligence that is needed – all their other advantages intact – to lead change all the way.

The big problem when it comes to change is that there are too many managers and too few leaders within companies – leaders who possess emotional intelligence which is the most important skill a leader embodies to empower change. A leader has what it takes to empower followership.

A manager tends to push and control, make decisions that he presupposes others to implement the way he expects. An emotionally competent leader leads by example and enhances followership on that journey because of the trust and respect he has earned.

In few words: SOFT SKILLS ARE THE NEW HARD SKILLS!

```html
<!DOCTYPE html>
<html lang="is">
<head>
<meta charset="utf-8">
<title>Uppspretta – og hugrekki hversdagsins</title>
<link rel="stylesheet" href="https://fonts.googleapis.com/css2?family=Libre+Franklin:wght@400;700;800&display=swap">
<style>
  :root {
    --cover-top: #b42a2d;
    --cover-mid: #cf5a45;
    --cover-bottom: #f39b7f;
    --title-white: #ffffff;
    --rule-light: rgba(255, 235, 225, 0.75);
    --glow: #ffe3d6;
    --art-mid: #e88a76;
    --author-red: #7c1a1c;
  }
  * { box-sizing: border-box; margin: 0; padding: 0; }
  html, body {
    width: 1200px;
    height: 1175px;
    overflow: hidden;
  }
  .book-cover {
    position: relative;
    width: 1200px;
    height: 1175px;
    background: linear-gradient(180deg, var(--cover-top) 0%, var(--cover-mid) 45%, var(--cover-bottom) 100%);
    font-family: "Libre Franklin", Arial, sans-serif;
    text-align: center;
    color: var(--title-white);
  }
  .book-title {
    position: absolute;
    top: 88px;
    left: 0;
    width: 100%;
    font-size: 132px;
    font-weight: 800;
    letter-spacing: 1px;
    line-height: 1;
  }
  .subtitle-block {
    position: absolute;
    top: 248px;
    left: 50%;
    width: 680px;
    transform: translateX(-50%);
  }
  .subtitle-rule {
    height: 1px;
    background: linear-gradient(90deg, transparent, var(--rule-light) 15%, var(--rule-light) 85%, transparent);
  }
  .book-subtitle {
    font-size: 46px;
    font-weight: 400;
    line-height: 1;
    padding: 20px 0 22px;
  }
  .cover-art {
    position: absolute;
    top: 370px;
    left: 240px;
    width: 720px;
    height: 650px;
    background: radial-gradient(ellipse 50% 48% at 52% 44%, var(--glow) 0%, var(--art-mid) 55%, transparent 100%);
  }
  .book-author {
    position: absolute;
    top: 1062px;
    left: 0;
    width: 100%;
    font-size: 50px;
    font-weight: 700;
    letter-spacing: 1px;
    color: var(--author-red);
    line-height: 1;
  }
</style>
</head>
<body>
  <main class="book-cover">
    <h1 class="book-title">UPPSPRETTA</h1>
    <div class="subtitle-block">
      <div class="subtitle-rule"></div>
      <p class="book-subtitle">og hugrekki hversdagsins</p>
      <div class="subtitle-rule"></div>
    </div>
    <div class="cover-art" role="img" aria-label="Illustration of a glowing globe circled by orbit lines, with silhouettes of business people meeting around a table in front of it"></div>
    <p class="book-author">HALLUR SIGMARSSON</p>
  </main>
</body>
</html>
```